Personal training and nutrition business needs business card design

We need a business card that outlays our services and invites potential customers to join our team and take the first step to a healthier and more enjoyable life. We cater for any level of fitness and specialize in weight loss and conditioning, strength training, muscle gain and strength endurance. Whether you are just starting off or need some help getting to the next level of your journey we are here to get the job done.
We specialize in one on one or one on two personal training sessions and each program will be custom made to suit individual fitness goals of our clients

```html
<!DOCTYPE html>
<html lang="en">
<head>
<meta charset="utf-8">
<title>Stride &amp; Core — Business Card</title>
<link href="https://fonts.googleapis.com/css2?family=Lato:wght@400;700;900&display=swap" rel="stylesheet">
<style>
  :root{
    --stage:#2b2b2d;
    --purple:#7a4a9e;
    --purple-light:#8a55ad;
    --orchid:#b064b8;
    --white:#ffffff;
    --ink:#111111;
  }
  *{margin:0;padding:0;box-sizing:border-box}
  html,body{width:1200px;height:1015px;overflow:hidden}
  body{
    background:var(--stage);
    font-family:"Lato",sans-serif;
    position:relative;
  }
  .card{
    position:absolute;
    left:320px;
    width:560px;height:320px;
    overflow:hidden;
    border-radius:2px;
    box-shadow:0 10px 30px rgba(0,0,0,.45);
  }
  .card--front{top:90px;background:linear-gradient(135deg,var(--purple) 0%,var(--purple-light) 100%)}
  .card--back{top:560px;background:var(--purple)}

  .front-brand{
    position:absolute;inset:0;
    display:flex;flex-direction:column;align-items:center;justify-content:center;
    color:var(--white);
  }
  .brand-row{display:flex;align-items:center;gap:14px}
  .brand-dot{width:22px;height:22px;border-radius:50%;background:var(--white);flex:none}
  .brand-name{font-weight:900;font-size:40px;letter-spacing:2px;text-transform:uppercase;line-height:1;white-space:nowrap}
  .brand-tagline{margin-top:10px;font-size:10px;letter-spacing:1.6px;text-transform:uppercase;font-weight:700;white-space:nowrap}

  .back-circle{position:absolute;left:0;top:0;width:560px;height:320px}
  .back-brand{
    position:absolute;left:330px;top:88px;width:220px;
    display:flex;flex-direction:column;align-items:center;text-align:center;
  }
  .back-brand .brand-dot{background:var(--purple);width:34px;height:34px;margin-bottom:12px}
  .back-brand .brand-name{color:var(--ink);font-size:30px;line-height:1.05}
  .back-brand .brand-tagline{color:var(--orchid);font-size:7.5px;letter-spacing:.8px;margin-top:8px}

  .contact{position:absolute;left:38px;top:54px;color:var(--white)}
  .contact-name{font-weight:700;font-size:20px;letter-spacing:.5px;text-transform:uppercase}
  .contact-role{font-size:15px;margin-top:2px}
  .contact-address{margin-top:58px;font-size:14px;line-height:1.25}
  .contact-lines{margin-top:14px;list-style:none;font-size:14px;line-height:1.45}
  .contact-lines li{display:flex;align-items:center;gap:8px}
  .contact-lines svg{width:14px;height:14px;flex:none}
</style>
</head>
<body>

<section class="card card--front" aria-label="Card front">
  <div class="front-brand">
    <div class="brand-row">
      <span class="brand-dot"></span>
      <span class="brand-name">Stride &amp; Core</span>
    </div>
    <p class="brand-tagline">Personal Training. Nutrition. Motivation</p>
  </div>
</section>

<section class="card card--back" aria-label="Card back">
  <svg class="back-circle" viewBox="0 0 560 320" aria-hidden="true">
    <circle cx="462" cy="118" r="200" fill="none" stroke="var(--orchid)" stroke-width="3"/>
    <circle cx="470" cy="112" r="200" fill="var(--white)"/>
  </svg>

  <div class="back-brand">
    <span class="brand-dot"></span>
    <span class="brand-name">Stride<br>&amp; Core</span>
    <p class="brand-tagline">Personal Training. Nutrition. Motivation</p>
  </div>

  <div class="contact">
    <h1 class="contact-name">Marcus Hale</h1>
    <p class="contact-role">Managing Director</p>
    <p class="contact-address">18 Harbour Lane<br>Westfield, 73190</p>
    <ul class="contact-lines">
      <li>
        <svg viewBox="0 0 24 24" fill="none" stroke="#fff" stroke-width="2"><path d="M5 3h4l2 5-2.5 1.5a11 11 0 0 0 6 6L16 13l5 2v4a2 2 0 0 1-2 2A16 16 0 0 1 3 5a2 2 0 0 1 2-2z"/></svg>
        044-555 018 274
      </li>
      <li>
        <svg viewBox="0 0 24 24" fill="none" stroke="#fff" stroke-width="2"><rect x="3" y="5" width="18" height="14"/><path d="M3 5l9 8 9-8"/></svg>
        hello@strideandcore.com
      </li>
      <li>
        <svg viewBox="0 0 24 24" fill="none" stroke="#fff" stroke-width="2"><circle cx="12" cy="12" r="9"/><path d="M3 12h18M12 3c3 3 3 15 0 18M12 3c-3 3-3 15 0 18"/></svg>
        www.strideandcore.com
      </li>
    </ul>
  </div>
</section>

</body>
</html>
```